Corvel Capital LLC

Need Professional Business cards for New Investment Fund

Target Market(s)

High Quality investors

Industry/Entity Type

Financial

Contact Information for Business Card

Phone Number +1 555 284 6190
Name Lukas Varenko
Title Fund Manager
email lv@FundCorvel.com
Website www.FundCorvel.com

Colors

Designer to choose colors to be used in the design.

Requirements
Must have
• Must have our Logo and all of the above. Must be made so lettering and loge can be raised

```html
<!DOCTYPE html>
<html lang="en">
<head>
<meta charset="utf-8">
<title>Orvessa – Business Card</title>
<link rel="stylesheet" href="https://fonts.googleapis.com/css2?family=Roboto:wght@400;500;700&display=swap">
<style>
  :root{
    --backdrop:#2a2a2a;
    --card:#1a1a1a;
    --accent:#7fba1f;
    --text:#e6e6e6;
    --wordmark-front:#3c3c3c;
    --wordmark-back:#f2f2f2;
    --icon-cut:#1a1a1a;
  }
  *{margin:0;padding:0;box-sizing:border-box}
  html,body{width:1200px;height:1138px;overflow:hidden;background:var(--backdrop)}
  body{position:relative;font-family:"Roboto",Arial,sans-serif;color:var(--text)}
  .card{position:absolute;width:620px;height:373px;background:var(--card);border-radius:16px}
  .card--front{left:275px;top:186px}
  .card--back{left:276px;top:608px}

  .wordmark{position:absolute;font-family:"Roboto",Arial,sans-serif;font-weight:500;letter-spacing:2px;line-height:1;display:flex;align-items:center;gap:12px;white-space:nowrap}
  .wordmark__square{width:14px;height:14px;background:currentColor}
  .card--front .wordmark{left:0;right:0;top:160px;justify-content:center;font-size:54px;color:var(--wordmark-front)}
  .card--back .wordmark{right:34px;top:92px;font-size:44px;color:var(--wordmark-back)}
  .card--back .wordmark__square{background:var(--accent)}

  .holder{position:absolute;left:35px;top:186px}
  .holder__name{font-size:25px;font-weight:700;color:var(--accent);line-height:1.2}
  .holder__title{font-size:17px;font-weight:400;margin-top:4px}

  .divider{position:absolute;left:35px;right:35px;top:262px;height:2px;background:var(--accent)}

  .contacts{position:absolute;left:36px;top:277px;list-style:none}
  .contacts li{display:flex;align-items:center;height:24px;font-size:16.5px}
  .contacts svg{width:16px;height:16px;margin-right:16px;fill:var(--accent)}

  .address{position:absolute;right:35px;top:301px;text-align:right;font-size:16.5px;line-height:24px;font-style:normal}
</style>
</head>
<body>
  <section class="card card--front" aria-label="Card front">
    <div class="wordmark"><span class="wordmark__square"></span>ORVESSA</div>
  </section>

  <section class="card card--back" aria-label="Card back">
    <div class="wordmark"><span class="wordmark__square"></span>ORVESSA</div>

    <div class="holder">
      <p class="holder__name">Lukas Varenko</p>
      <p class="holder__title">Fund Manager</p>
    </div>

    <div class="divider"></div>

    <ul class="contacts">
      <li>
        <svg viewBox="0 0 16 16" aria-hidden="true"><path d="M2 6c0-2 2-3 6-3s6 1 6 3v1h-3V5.5H5V7H2z"/><rect x="3" y="8" width="10" height="6" rx="1"/></svg>
        +1 555 284 6190
      </li>
      <li>
        <svg viewBox="0 0 16 16" aria-hidden="true"><path d="M1 3h14v10H1z M2 4l6 5 6-5" stroke="var(--icon-cut)" stroke-width="1.2"/></svg>
        lv@FundCorvel.com
      </li>
      <li>
        <svg viewBox="0 0 16 16" aria-hidden="true"><circle cx="8" cy="8" r="7"/><path d="M1 8h14M8 1c3 3 3 11 0 14M8 1c-3 3-3 11 0 14" stroke="var(--icon-cut)" stroke-width="1" fill="none"/></svg>
        www.FundCorvel.com
      </li>
    </ul>

    <address class="address">48 Alder Ave.<br>Fairview, NJ, 07022</address>
  </section>
</body>
</html>
```